Health and Wellness company needs flyer to promote free seminar

Corvella Motion studio is a health and wellness company that offers an exercise program designed by physical therapists to help relieve pain and improve mobility. Our business is a new concept that is not well understood by the public. In order to promote our business we offer a free seminar where we present information regarding the underlying cause of pain and tightness. During the seminar we also perform a posture screen and movement testing for all participants.

Target Market(s)

Mostly healthy and active women ages 25-65

Industry/Entity Type

Health And Wellness

Font styles to use
Sans Serif

Colors

Designer to choose colors to be used in the design.

Requirements
Must have
• Title: Eliminate Pain and Tightness For Good
• Paragraph: Corvella Motion Studio offers a free 60 minute seminar: "The Busy Walker's Manual for Stretching and Living Lighter."
• What to Expect:
• • Identify the underlying cause of your pain and mobility issues
• • Expose what gets in the way of you moving and feeling better
• • Learn why traditional exercises don’t help and can actually make the problem worse
• • Reveal what your posture is saying and how that impacts you
• • Experience your muscle imbalances through movement tests
• • Discover the training method that realigns your posture, increases your mobility and reduces your pain
• Call to action: RSVP online at corvellamotionstudio.com
Nice to have
• Use a relevant image showing a female dealing with tightness in the low back, legs, etc.
• Emphasize that the seminar is FREE.
• Make the call to action prominent.

```html
<!DOCTYPE html>
<html lang="en">
<head>
<meta charset="utf-8">
<title>Corvella Motion Studio – Free Seminar Flyer</title>
<link href="https://fonts.googleapis.com/css2?family=Bebas+Neue&family=Crimson+Text&family=Open+Sans:wght@400;600;700&family=Mulish:ital,wght@1,600&display=swap" rel="stylesheet">
<style>
  :root {
    --indigo: #3f4491;
    --orange: #ee8a1d;
    --paper: #f4f4f7;
    --ink: #3b3b44;
    --stage: #d9d3cd;
  }
  * { margin: 0; padding: 0; box-sizing: border-box; }
  html, body { width: 1200px; height: 1093px; overflow: hidden; background: var(--stage); }
  .flyer {
    position: absolute; left: 200px; top: 26px;
    width: 800px; height: 1040px;
    background: var(--paper);
    overflow: hidden;
    box-shadow: 0 6px 24px rgba(0,0,0,.18);
    font-family: "Open Sans", sans-serif;
    color: var(--ink);
  }
  .flyer__shapes { position: absolute; inset: 0; }
  .brand {
    position: absolute; left: 475px; top: 92px;
    display: flex; align-items: center; gap: 12px;
  }
  .brand__square { width: 30px; height: 30px; background: var(--orange); flex: none; }
  .brand__name {
    font-weight: 700; font-size: 20px; color: var(--indigo); white-space: nowrap;
  }
  .presents {
    position: absolute; left: 470px; top: 150px; width: 310px;
    text-align: center; line-height: 1.2;
    font-family: "Crimson Text", serif; font-size: 52px; color: var(--orange);
  }
  .headline {
    position: absolute; left: 470px; top: 232px; width: 310px;
    border-top: 4px solid var(--indigo);
    border-bottom: 4px solid var(--indigo);
    padding: 10px 0 8px;
    font-family: "Bebas Neue", sans-serif; font-weight: 400; line-height: 1.05;
    white-space: nowrap;
  }
  .headline__guide { display: block; font-size: 46px; color: var(--indigo); }
  .headline__free { display: block; font-size: 58px; color: var(--orange); }
  .tagline {
    position: absolute; left: 0; width: 800px; top: 574px; text-align: center;
    font-family: "Mulish", sans-serif; font-style: italic; font-weight: 600;
    font-size: 26px; color: #fff;
  }
  .expect { position: absolute; left: 110px; top: 672px; width: 600px; }
  .expect__title {
    font-family: "Bebas Neue", sans-serif; font-weight: 400; font-size: 30px;
    color: var(--indigo); margin-bottom: 10px; letter-spacing: .5px;
  }
  .expect__list { list-style: none; }
  .expect__item {
    position: relative; padding-left: 44px; margin-bottom: 6px;
    font-size: 15.5px; line-height: 1.5;
  }
  .expect__tick { position: absolute; left: 0; top: 3px; width: 18px; height: 18px; }
  .expect__verb {
    color: var(--orange); font-weight: 700;
    border-bottom: 2px solid var(--indigo);
  }
  .cta {
    position: absolute; left: 0; width: 800px; top: 988px; text-align: center;
    font-size: 24px; color: #fff;
  }
  .cta__url { color: var(--orange); font-weight: 700; }
</style>
</head>
<body>
<main class="flyer">
  <svg class="flyer__shapes" viewBox="0 0 800 1040" width="800" height="1040">
    <defs>
      <linearGradient id="tint" x1="0" y1="0" x2="1" y2="1">
        <stop offset="0" stop-color="#f3f3f8"/>
        <stop offset="1" stop-color="#e6e6f4"/>
      </linearGradient>
      <linearGradient id="photoTone" x1="0" y1="0" x2="0" y2="1">
        <stop offset="0" stop-color="#b8805a"/>
        <stop offset=".35" stop-color="#e9e6e8"/>
        <stop offset=".6" stop-color="#a66c49"/>
        <stop offset=".75" stop-color="#ef6c9a"/>
        <stop offset="1" stop-color="#e85b8c"/>
      </linearGradient>
    </defs>
    <rect class="header-bg" x="0" y="0" width="800" height="620" fill="url(#tint)"/>
    <rect class="hero-photo" x="20" y="0" width="420" height="600" rx="6" fill="url(#photoTone)"
          role="img" aria-label="Photo of an active woman seen from behind, in a sports top and pink shorts, holding her lower back"/>
    <path class="wave-orange" d="M0,455 Q260,560 800,520 L800,540 Q280,580 0,490 Z" fill="var(--orange)"/>
    <path class="wave-band" d="M0,488 Q300,575 800,530 L800,640 Q430,612 0,655 Z" fill="var(--indigo)"/>
    <path class="wave-orange-low" d="M430,624 Q660,614 800,635 L800,655 Q660,630 430,624 Z" fill="var(--orange)"/>
    <path class="footer-line" d="M0,980 Q420,930 800,960" fill="none" stroke="#d6d6e6" stroke-width="12"/>
    <path class="footer-band" d="M0,995 Q420,945 800,975 L800,1040 L0,1040 Z" fill="var(--indigo)"/>
  </svg>

  <div class="brand">
    <span class="brand__square"></span>
    <span class="brand__name">Corvella Motion Studio</span>
  </div>

  <p class="presents">presents</p>

  <h1 class="headline">
    <span class="headline__guide">The Busy Walker's</span>
    <span class="headline__guide">Manual</span>
    <span class="headline__free">Free Seminar</span>
  </h1>

  <p class="tagline">Eliminate Pain and Tightness for Good.</p>

  <section class="expect">
    <h2 class="expect__title">What to Expect:</h2>
    <ul class="expect__list">
      <li class="expect__item"><svg class="expect__tick" viewBox="0 0 20 20"><circle cx="10" cy="10" r="8.5" fill="none" stroke="var(--indigo)" stroke-width="2"/><path d="M6 10.2l2.8 2.8L14 7.6" fill="none" stroke="var(--indigo)" stroke-width="2"/></svg><span class="expect__verb">Identify</span> the underlying cause of your pain and mobility issues</li>
      <li class="expect__item"><svg class="expect__tick" viewBox="0 0 20 20"><circle cx="10" cy="10" r="8.5" fill="none" stroke="var(--indigo)" stroke-width="2"/><path d="M6 10.2l2.8 2.8L14 7.6" fill="none" stroke="var(--indigo)" stroke-width="2"/></svg><span class="expect__verb">Expose</span> what gets in the way of you moving and feeling better</li>
      <li class="expect__item"><svg class="expect__tick" viewBox="0 0 20 20"><circle cx="10" cy="10" r="8.5" fill="none" stroke="var(--indigo)" stroke-width="2"/><path d="M6 10.2l2.8 2.8L14 7.6" fill="none" stroke="var(--indigo)" stroke-width="2"/></svg><span class="expect__verb">Learn</span> why traditional exercises don’t help and can actually make the problem worse</li>
      <li class="expect__item"><svg class="expect__tick" viewBox="0 0 20 20"><circle cx="10" cy="10" r="8.5" fill="none" stroke="var(--indigo)" stroke-width="2"/><path d="M6 10.2l2.8 2.8L14 7.6" fill="none" stroke="var(--indigo)" stroke-width="2"/></svg><span class="expect__verb">Reveal</span> what your posture is saying and how that impacts you</li>
      <li class="expect__item"><svg class="expect__tick" viewBox="0 0 20 20"><circle cx="10" cy="10" r="8.5" fill="none" stroke="var(--indigo)" stroke-width="2"/><path d="M6 10.2l2.8 2.8L14 7.6" fill="none" stroke="var(--indigo)" stroke-width="2"/></svg><span class="expect__verb">Experience</span> your muscle imbalances through movement tests</li>
      <li class="expect__item"><svg class="expect__tick" viewBox="0 0 20 20"><circle cx="10" cy="10" r="8.5" fill="none" stroke="var(--indigo)" stroke-width="2"/><path d="M6 10.2l2.8 2.8L14 7.6" fill="none" stroke="var(--indigo)" stroke-width="2"/></svg><span class="expect__verb">Discover</span> the training method that realigns your posture, increases your mobility and reduces your pain</li>
    </ul>
  </section>

  <p class="cta">RSVP online at <span class="cta__url">corvellamotionstudio.com</span></p>
</main>
</body>
</html>
```